School Poster

Design so that these can be placed in classrooms across the school.

Attached is another design we have had done. Use a similar theme.

Consider using themes from https://corvalhs.edq.example.au/

please edit Binder1 doc.

Students and teachers

```html
<!DOCTYPE html>
<html lang="en">
<head>
<meta charset="utf-8">
<title>Before You Ask the Teacher – Classroom Poster</title>
<link rel="stylesheet" href="https://fonts.googleapis.com/css2?family=Poppins:wght@400;500;600;700;800&family=Dancing+Script:wght@600&display=swap">
<style>
:root{
  --navy:#0d1b45;
  --navy-deep:#08163a;
  --blue:#1f4f9c;
  --sky:#2f86d6;
  --gold:#fbc72b;
  --gold-soft:#f8d977;
  --ice:#e3eaf6;
  --line:#6f9bd6;
  --red:#e53935;
  --stage:#777777;
  --white:#ffffff;
}
*{box-sizing:border-box;margin:0;padding:0}
html,body{width:1012px;height:1200px;overflow:hidden;background:var(--stage);font-family:"Poppins",sans-serif;color:var(--navy)}
.poster{position:absolute;left:113px;top:56px;width:768px;height:1087px;background:var(--white);overflow:hidden}
.poster-waves{position:absolute;inset:0;z-index:0}
.brand{position:absolute;left:62px;top:122px;z-index:2;display:flex;align-items:center;gap:12px}
.brand-mark{flex:none;width:40px;height:40px;background:var(--blue)}
.brand-name{font-weight:700;font-size:18px;color:var(--blue);line-height:1.15;width:130px}
.headline{position:absolute;left:342px;top:80px;z-index:2}
.headline-top{font-weight:800;font-size:37px;line-height:1;letter-spacing:.3px;color:var(--navy)}
.headline-main{font-weight:800;font-size:55px;line-height:1;letter-spacing:-1px;color:var(--blue);margin-top:2px}
.headline-pill{margin-top:6px;display:inline-block;width:324px;height:32px;border-radius:16px;background:linear-gradient(90deg,var(--navy-deep) 60%,var(--blue));color:var(--white);font-weight:800;font-size:21px;line-height:32px;padding-left:17px}
.steps{position:absolute;left:36px;top:229px;width:699px;height:322px;z-index:1}
.steps-frame{position:absolute;inset:0}
.step{position:absolute;top:0;height:276px}
.step-1{left:0;width:216px}
.step-2{left:216px;width:235px}
.step-3{left:451px;width:248px}
.step-num{position:absolute;top:9px;width:37px;height:37px;border-radius:50%;background:var(--gold);font-weight:600;font-size:22px;line-height:37px;text-align:center;color:var(--navy)}
.step-1 .step-num{left:10px}.step-2 .step-num{left:21px}.step-3 .step-num{left:29px}
.step-icon{position:absolute;top:18px;width:70px;height:72px;border-radius:10px;background:linear-gradient(135deg,#f4d57a,#c9d6ee)}
.step-1 .step-icon{left:70px}.step-2 .step-icon{left:85px}.step-3 .step-icon{left:97px}
.step-title{position:absolute;top:116px;height:27px;border-radius:14px;background:var(--navy);color:var(--white);font-weight:600;font-size:13.5px;line-height:27px;text-align:center}
.step-title em{font-style:normal;color:var(--gold)}
.step-1 .step-title{left:16px;width:188px}
.step-2 .step-title{left:13px;width:188px}
.step-3 .step-title{left:21px;width:188px}
.step-lead{position:absolute;top:149px;font-weight:600;font-size:12.5px;line-height:1.25}
.step-1 .step-lead{left:24px}.step-2 .step-lead{left:17px}.step-3 .step-lead{left:27px;width:200px}
.checks{position:absolute;list-style:none;font-size:10px;line-height:1.62}
.checks li{position:relative;padding-left:13px}
.checks li::before{content:"";position:absolute;left:0;top:4px;width:8px;height:8px;border:1.2px solid var(--gold);border-radius:50%}
.checks li::after{content:"";position:absolute;left:2.6px;top:5.4px;width:2.6px;height:4.2px;border-right:1.3px solid var(--gold);border-bottom:1.3px solid var(--gold);transform:rotate(40deg)}
.step-1 .checks{left:23px;top:179px;line-height:1.65}
.step-2 .checks{left:34px;top:179px;line-height:1.33}
.step-3 .checks{left:22px;top:188px;line-height:1.32;font-size:9.6px}
.step-note{position:absolute;left:13px;top:238px;font-weight:600;font-size:12px}
.values{position:absolute;left:0;top:276px;width:699px;height:46px;display:flex;align-items:center}
.value{flex:1;display:flex;align-items:center;justify-content:center;gap:9px;color:var(--white);font-weight:700;font-size:18px}
.value + .value{border-left:1.5px dotted var(--gold)}
.value-icon{width:24px;height:22px;border-radius:4px;background:var(--gold);opacity:.85}
.section-title{position:absolute;left:0;width:768px;top:572px;text-align:center;font-weight:800;font-size:22px;letter-spacing:.2px;color:var(--navy)}
.rule-box{position:absolute;left:48px;width:672px;border-radius:10px;z-index:1}
.rule-must{top:608px;height:116px;background:linear-gradient(100deg,var(--gold) 70%,var(--gold-soft))}
.rule-approved{top:732px;height:116px;background:linear-gradient(100deg,var(--navy-deep) 65%,#233d82)}
.rule-box h3{position:absolute;left:26px;top:11px;font-weight:600;font-size:16px}
.rule-approved h3{color:var(--white);font-weight:500}
.rule-box .checks{left:26px;top:38px;font-size:11px;line-height:1.38}
.rule-box .checks li{padding-left:19px}
.rule-box .checks li::before{width:11px;height:11px;top:3px;border-color:var(--navy);border-width:1.5px}
.rule-box .checks li::after{left:3.8px;top:4.6px;width:3.4px;height:6px;border-color:var(--navy);border-width:0 1.7px 1.7px 0}
.rule-approved .checks{color:var(--white)}
.rule-approved .checks li::before,.rule-approved .checks li::after{border-color:var(--gold)}
.rule-art{position:absolute;top:12px;right:28px;width:108px;height:94px;border-radius:10px}
.rule-must .rule-art{background:linear-gradient(135deg,#e8b923,#f5d469)}
.rule-approved .rule-art{background:linear-gradient(135deg,#2c4d96,#1a2e66)}
.rule-cannot{position:absolute;left:48px;top:858px;width:672px;height:152px;border:1px solid var(--line);border-radius:10px;background:var(--ice);z-index:1}
.cannot-tab{position:absolute;left:226px;top:-1px;width:221px;height:30px;border-radius:0 0 16px 16px;background:#4f6fa8;color:var(--white);font-weight:500;font-size:16px;line-height:28px;text-align:center}
.cannot-list{position:absolute;left:0;top:42px;width:100%;display:flex;list-style:none}
.cannot-list li{position:relative;height:98px;text-align:center;font-weight:500;font-size:11.6px;line-height:1.35;padding:34px 8px 0}
.cannot-list li::before{content:"";position:absolute;left:50%;top:0;width:27px;height:27px;margin-left:-13.5px;border-radius:50%;background:var(--red)}
.cannot-list li::after{content:"×";position:absolute;left:50%;top:-5px;margin-left:-6px;color:var(--white);font-size:24px;font-weight:600;line-height:1.4}
.cannot-list li + li{border-left:1px solid var(--navy)}
.cannot-list li:nth-child(1){width:160px}
.cannot-list li:nth-child(2){width:175px}
.cannot-list li:nth-child(3){width:155px}
.cannot-list li:nth-child(4){width:182px}
.site-url{position:absolute;right:48px;top:1020px;z-index:1;font-size:13.5px;color:var(--navy)}
.closing{position:absolute;left:54px;top:1026px;z-index:1;color:var(--white)}
.closing-line{font-weight:500;font-size:13px}
.closing-script{font-family:"Dancing Script",cursive;font-size:20px;color:var(--gold);line-height:1.1}
</style>
</head>
<body>
<main class="poster">
  <svg class="poster-waves" width="768" height="1087" viewBox="0 0 768 1087" aria-hidden="true">
    <path d="M0 0H768V52C610 18 430 30 300 80C200 116 80 110 0 92Z" fill="#1f4f9c" opacity=".9"/>
    <path d="M0 0H768V44C600 12 420 22 300 70C200 104 80 100 0 84Z" fill="#0d1b45"/>
    <path d="M0 975C170 950 320 990 470 1030C610 1066 700 1060 768 1046V1087H0Z" fill="#2f86d6"/>
    <path d="M0 985C170 962 320 1002 470 1042C610 1078 700 1072 768 1060V1087H0Z" fill="#0d1b45"/>
    <path d="M0 1000C140 986 280 1020 430 1060C520 1082 560 1087 600 1087H0Z" fill="#173a80" opacity=".55"/>
  </svg>

  <div class="brand">
    <span class="brand-mark"></span>
    <span class="brand-name">Corval State High</span>
  </div>

  <header class="headline">
    <h1 class="headline-top">BEFORE YOU ASK</h1>
    <div class="headline-main">THE TEACHER...</div>
    <div class="headline-pill">TRY THESE STEPS FIRST!</div>
  </header>

  <section class="steps">
    <svg class="steps-frame" width="699" height="322" viewBox="0 0 699 322" aria-hidden="true">
      <path d="M0.5 276V12Q0.5 0.5 12 0.5H210L236 45L216 84V276" fill="none" stroke="#6f9bd6"/>
      <path d="M252 0.5H448L473 45L451 84V276" fill="none" stroke="#6f9bd6"/>
      <path d="M467 0.5H688Q698.5 0.5 698.5 12V276" fill="none" stroke="#6f9bd6"/>
      <path d="M0 270H699V308Q699 322 685 322H14Q0 322 0 308Z" fill="#0d1b45"/>
    </svg>

    <article class="step step-1">
      <div class="step-num">1</div>
      <div class="step-icon" role="img" aria-label="Line icon of a head with gears"></div>
      <h2 class="step-title">THINK <em>FIRST</em></h2>
      <p class="step-lead">Don’t give up away.</p>
      <ul class="checks">
        <li>Read the question carefully.</li>
        <li>Try a strategy you’ve used before.</li>
        <li>Indentify what you already know</li>
        <li>Give yourself thinking time.</li>
      </ul>
    </article>

    <article class="step step-2">
      <div class="step-num">2</div>
      <div class="step-icon" role="img" aria-label="Line icon of two hands clasped"></div>
      <h2 class="step-title">CHECK YOUR <em>SUPPORTS</em></h2>
      <p class="step-lead">Before asking for help, check</p>
      <ul class="checks">
        <li>Learning goal and success criteria.</li>
        <li>Worked examples.</li>
        <li>Class notes.</li>
        <li>Classroom displays.</li>
        <li>ClassHub resources.</li>
        <li>Task sheet and instructions.</li>
      </ul>
    </article>

    <article class="step step-3">
      <div class="step-num">3</div>
      <div class="step-icon" role="img" aria-label="Line icon of a student raising a hand with a question bubble"></div>
      <h2 class="step-title">ASK 3 <em>BEFORE ME</em></h2>
      <p class="step-lead">Ask three sources before asking the teacher:</p>
      <ul class="checks">
        <li>A person (partner or neighbour)</li>
        <li>A resource (worked example, task sheet)</li>
        <li>A place (notes, displays, ClassHub)</li>
      </ul>
      <p class="step-note">A place (notes, displays, ClassHub)</p>
    </article>

    <div class="values">
      <div class="value"><span class="value-icon" role="img" aria-label="Icon of a hand"></span>WE BELIEVE</div>
      <div class="value"><span class="value-icon" role="img" aria-label="Icon of a figure climbing steps"></span>WE STRIVE</div>
      <div class="value"><span class="value-icon" role="img" aria-label="Icon of a trophy"></span>WE ACHIEVE</div>
    </div>
  </section>

  <h2 class="section-title">USING AI AND OTHER TOOLS RESPONSIBLY</h2>

  <section class="rule-box rule-must">
    <h3>What You Must Do:</h3>
    <ul class="checks">
      <li>Complete your own work</li>
      <li>Demostrate your progress (drafts, notes, planning, revisions)</li>
      <li>Use feedback to imporve your work</li>
      <li>Demostrate your understanding of the ideas in your submission</li>
    </ul>
    <div class="rule-art" role="img" aria-label="Line icon of a head with a brain and sparkles"></div>
  </section>

  <section class="rule-box rule-approved">
    <h3>What You Must Do: (when approved by your teacher)</h3>
    <ul class="checks">
      <li>Brainstorm ideas</li>
      <li>Check spelling, grammer and clarity</li>
      <li>Read your work aloud using text-to-speech tools</li>
      <li>Help indentify areas for improvement in a draft</li>
    </ul>
    <div class="rule-art" role="img" aria-label="Line icon of a computer monitor with AI and a gear"></div>
  </section>

  <section class="rule-cannot">
    <div class="cannot-tab">What Your Cannot Do:</div>
    <ul class="cannot-list">
      <li>Submit<br>AI-generated<br>work as yourown</li>
      <li>Copy and paste AI responses without acknowledging or adapting them</li>
      <li>Use AI tools to complete the whole task for you</li>
      <li>Submit work that does not demostrate your understanding</li>
    </ul>
  </section>

  <div class="site-url">WWW.corvalhs.edq.example.au</div>

  <footer class="closing">
    <p class="closing-line">If you didn’t create, develop and understnad it,</p>
    <p class="closing-script">it isn’t your work.</p>
  </footer>
</main>
</body>
</html>
```